Powerpoint Presentation (urgent)

We need a powerpoint presentation to accompany our other pitch materials for a really exciting, new project.

It is a project related to gaming.

The presentation should be engaging, professionally done, and be trendy and captivating.

```html
<!DOCTYPE html>
<html lang="en">
<head>
<meta charset="utf-8">
<title>PIXELFORGE Pitch Deck</title>
<link href="https://fonts.googleapis.com/css2?family=Raleway:wght@300;400;600;700;800&display=swap" rel="stylesheet">
<style>
:root{
  --red:#c8102e;
  --ink:#1c1c1c;
  --dark:#232323;
  --grey:#8a8a8a;
  --light-grey:#b5b5b5;
  --paper:#ffffff;
  --sheet:#ececec;
}
*{margin:0;padding:0;box-sizing:border-box}
html,body{width:1200px;height:893px;overflow:hidden;background:var(--sheet);font-family:'Raleway',sans-serif;color:var(--ink)}
.sheet{display:grid;grid-template-columns:repeat(3,384px);grid-auto-rows:216px;column-gap:16px;row-gap:6.5px;padding:3px 8px}
.slide{position:relative;background:var(--paper);overflow:hidden;box-shadow:0 1px 3px rgba(0,0,0,.18)}
.abs{position:absolute}
.photo{position:absolute}
.photo-dark{background:linear-gradient(135deg,#3a3a3a,#151515)}
.photo-warm{background:linear-gradient(135deg,#8c7a6a,#4e5a63 60%,#2e3540)}
.photo-park{background:linear-gradient(120deg,#6f6a5e,#3d4a52 55%,#2b2f36)}
.photo-green{background:linear-gradient(135deg,#9aa27a,#6a5a55 55%,#3c4a66)}

/* brand wordmark */
.brand{position:absolute;text-align:center;line-height:1}
.brand-name{font-weight:800;color:var(--red);letter-spacing:.02em;display:block}
.brand-tag{display:block;color:var(--ink);letter-spacing:.3em;font-weight:400}
.brand.sm .brand-name{font-size:7.5px}
.brand.sm .brand-tag{font-size:3.6px;margin-top:1.5px}
.brand.on-dark .brand-tag{color:#fff}

/* footer */
.footer{position:absolute;left:0;right:0;bottom:0;height:11px;background:var(--red);color:#fff;font-size:4px;display:flex;justify-content:space-between;align-items:center;padding:0 6px}

/* headings */
.slide-title{position:absolute;left:17px;top:17px;font-size:17px;font-weight:600;letter-spacing:-.01em}
.slide-title::after{content:"";display:block;width:19px;height:1.5px;background:var(--red);margin-top:3px}
.lorem{font-size:4.6px;line-height:1.35;color:var(--light-grey)}
.cover-title{font-weight:300;color:#fff;text-align:center}

/* slide 1 */
.s1 .brand .brand-name{font-size:28px}
.s1 .brand .brand-tag{font-size:12px;margin-top:6px;letter-spacing:.35em}

/* presenters */
.presenters{position:absolute;display:flex;align-items:center;gap:14px;font-size:6px}
.presenter{display:flex;align-items:center;gap:3px}
.presenter b{font-weight:400;display:block}
.presenter i{font-style:normal;color:var(--red);font-size:3.4px;display:block}
.presenter svg{width:7px;height:7px}
.by{font-size:3px;color:var(--grey)}

/* agenda */
.agenda-item{position:absolute;display:flex;gap:10px}
.icon-box{width:13px;height:13px;background:var(--ink);display:flex;align-items:center;justify-content:center;flex:none;margin-top:2px}
.agenda-item h4{font-weight:400;font-size:7.5px;color:#444}
.agenda-item .time{font-size:3.8px;color:var(--red)}
.agenda-item .lorem{width:104px}

/* services */
.service{position:absolute;left:210px;display:flex;gap:10px;width:160px}
.round-icon{width:16px;height:16px;border-radius:50%;background:var(--ink);flex:none;display:flex;align-items:center;justify-content:center;margin-top:1px}
.service h4{font-weight:400;font-size:7.5px;color:#333}

/* previous work badges */
.badge{position:absolute;border:1.2px solid #333}

/* text area */
.lead{font-weight:700;font-size:8.8px;line-height:1.3;color:var(--ink)}
.para{font-size:6.3px;line-height:1.35;color:#a0a0a0;margin-top:8px}
</style>
</head>
<body>
<main class="sheet">

  <!-- 1 cover -->
  <section class="slide s1">
    <div class="photo photo-dark" style="inset:0" role="img" aria-label="Darkened photo of a gaming setup"></div>
    <div class="brand on-dark" style="left:0;right:0;top:120px">
      <span class="brand-name">PIXELFORGE</span>
      <span class="brand-tag">TAGLINE HERE</span>
    </div>
  </section>

  <!-- 2 title -->
  <section class="slide">
    <div class="photo photo-dark" style="left:0;top:0;width:384px;height:161px" role="img" aria-label="Darkened photo of people gaming on a sofa"></div>
    <p class="cover-title abs" style="left:0;right:0;top:119px;font-size:18px">Your Title Goes Here</p>
    <p class="cover-title abs" style="left:0;right:0;top:142px;font-size:6.5px">Your Subtitle Goes Here</p>
    <div class="brand sm" style="left:20px;top:182px"><span class="brand-name">PIXELFORGE</span><span class="brand-tag">TAGLINE HERE</span></div>
    <div class="presenters" style="right:35px;top:186px">
      <span class="by">Presented by</span>
      <span class="presenter"><svg viewBox="0 0 10 10"><circle cx="5" cy="3" r="2.4" fill="#333"/><path d="M0 10a5 4.5 0 0 1 10 0z" fill="#333"/></svg><span><b>Alex Reed</b><i>VP Marketing</i></span></span>
      <span class="presenter"><svg viewBox="0 0 10 10"><circle cx="5" cy="3" r="2.4" fill="#333"/><path d="M0 10a5 4.5 0 0 1 10 0z" fill="#333"/></svg><span><b>Mia Stone</b><i>Senior Consultant</i></span></span>
    </div>
    <div class="abs" style="left:0;right:0;bottom:0;height:9px;background:var(--red)"></div>
  </section>

  <!-- 3 title with photo -->
  <section class="slide">
    <div class="photo photo-warm" style="left:0;top:26px;width:384px;height:166px" role="img" aria-label="Photo of two friends playing on a phone"></div>
    <svg class="abs" style="left:0;top:0" width="384" height="80" viewBox="0 0 384 80"><path d="M0 0H384V26H215C195 26 188 60 160 60H0Z" fill="#fff"/></svg>
    <div class="brand sm" style="left:22px;top:38px;text-align:left"><span class="brand-name" style="font-size:9px">PIXELFORGE</span><span class="brand-tag">TAGLINE HERE</span></div>
    <div class="abs" style="left:0;right:0;top:152px;height:40px;background:rgba(20,20,20,.55)"></div>
    <p class="cover-title abs" style="left:90px;right:0;top:158px;font-size:17px">Your Title Goes Here</p>
    <p class="cover-title abs" style="left:90px;right:0;top:179px;font-size:6px">Your Subtitle Goes Here</p>
    <div class="presenters" style="left:6px;top:200px;gap:10px">
      <span class="by">Presented by</span>
      <span class="presenter"><svg viewBox="0 0 10 10"><circle cx="5" cy="3" r="2.4" fill="#333"/><path d="M0 10a5 4.5 0 0 1 10 0z" fill="#333"/></svg><span><b style="color:var(--red)">Alex Reed</b><i style="color:#555">VP Marketing</i></span></span>
      <span class="presenter"><svg viewBox="0 0 10 10"><circle cx="5" cy="3" r="2.4" fill="#333"/><path d="M0 10a5 4.5 0 0 1 10 0z" fill="#333"/></svg><span><b style="color:var(--red)">Mia Stone</b><i style="color:#555">Senior Consultant</i></span></span>
      <span style="width:1px;height:12px;background:#999"></span>
      <span class="by">Presented by</span>
      <span class="presenter"><svg viewBox="0 0 10 10"><circle cx="5" cy="3" r="2.4" fill="#333"/><path d="M0 10a5 4.5 0 0 1 10 0z" fill="#333"/></svg><span><b style="color:var(--red)">Sam Cole</b><i style="color:#555">Vice President</i></span></span>
    </div>
    <p class="abs" style="right:8px;top:204px;font-size:4.6px;color:var(--grey)">Cityname | November 28, 2017</p>
  </section>

  <!-- 4 quote dark -->
  <section class="slide">
    <div class="photo photo-dark" style="inset:0" role="img" aria-label="Darkened photo of a workshop"></div>
    <div class="abs" style="left:175px;top:55px;width:34px;height:34px;border-radius:50%;background:#fff;color:var(--red);font-weight:800;font-size:30px;text-align:center;line-height:44px">“</div>
    <p class="cover-title abs" style="left:0;right:0;top:97px;font-size:12.5px;line-height:1.24">Coming together is a beginning.<br>Keeping together is progress.<br>Working together is success.</p>
    <p class="cover-title abs" style="left:0;right:0;top:156px;font-size:6.5px;color:#ccc">- Walter Grey -</p>
  </section>

  <!-- 5 agenda -->
  <section class="slide">
    <h2 class="slide-title">Our Agenda</h2>
    <div class="brand sm" style="right:13px;top:28px"><span class="brand-name">PIXELFORGE</span><span class="brand-tag">TAGLINE HERE</span></div>
    <div class="agenda-item" style="left:53px;top:58px"><span class="icon-box"><svg width="8" height="8" viewBox="0 0 10 10"><circle cx="5" cy="5" r="4" fill="none" stroke="#fff" stroke-width="1.2"/><path d="M5 2.5V5l2 1" stroke="#fff" fill="none"/></svg></span><div><h4>Agenda One</h4><p class="time">10:00</p><p class="lorem">Lorem ipsum dolor sit amet, consectetur adipiscing elit, sed do eiusmod tempor labore.</p></div></div>
    <div class="agenda-item" style="left:53px;top:104px"><span class="icon-box"><svg width="8" height="8" viewBox="0 0 10 10"><circle cx="5" cy="5" r="4" fill="none" stroke="#fff" stroke-width="1.2"/><path d="M5 2.5V5l2 1" stroke="#fff" fill="none"/></svg></span><div><h4>Agenda Two</h4><p class="time">11:00</p><p class="lorem">Lorem ipsum dolor sit amet, consectetur adipiscing elit, sed do eiusmod labore.</p></div></div>
    <div class="agenda-item" style="left:53px;top:148px"><span class="icon-box"><svg width="8" height="8" viewBox="0 0 10 10"><circle cx="5" cy="5" r="4" fill="none" stroke="#fff" stroke-width="1.2"/><path d="M5 2.5V5l2 1" stroke="#fff" fill="none"/></svg></span><div><h4>Agenda Three</h4><p class="time">12:00</p><p class="lorem">Lorem ipsum dolor sit amet, consectetur adipiscing elit, sed do eiusmod tempor labore.</p></div></div>
    <div class="agenda-item" style="left:208px;top:58px"><span class="icon-box"><svg width="8" height="8" viewBox="0 0 10 10"><circle cx="5" cy="5" r="4" fill="none" stroke="#fff" stroke-width="1.2"/><path d="M5 2.5V5l2 1" stroke="#fff" fill="none"/></svg></span><div><h4>Agenda Four</h4><p class="time">13:00</p><p class="lorem">Lorem ipsum dolor sit amet, consectetur adipiscing elit, sed do eiusmod tempor labore.</p></div></div>
    <div class="agenda-item" style="left:208px;top:104px"><span class="icon-box"><svg width="8" height="8" viewBox="0 0 10 10"><circle cx="5" cy="5" r="4" fill="none" stroke="#fff" stroke-width="1.2"/><path d="M5 2.5V5l2 1" stroke="#fff" fill="none"/></svg></span><div><h4>Agenda Five</h4><p class="time">14:00</p><p class="lorem">Lorem ipsum dolor sit amet, consectetur adipiscing elit, sed do eiusmod tempor labore.</p></div></div>
    <div class="agenda-item" style="left:208px;top:148px"><span class="icon-box"><svg width="8" height="8" viewBox="0 0 10 10"><circle cx="5" cy="5" r="4" fill="none" stroke="#fff" stroke-width="1.2"/><path d="M5 2.5V5l2 1" stroke="#fff" fill="none"/></svg></span><div><h4>Agenda Six</h4><p class="time">15:00</p><p class="lorem">Lorem ipsum dolor sit amet, consectetur adipiscing elit, sed do eiusmod tempor labore.</p></div></div>
    <div class="footer"><span>© 2017 PIXELFORGE All rights reserved</span><span>5</span></div>
  </section>

  <!-- 6 about -->
  <section class="slide">
    <div class="photo photo-park" style="left:0;top:0;width:268px;height:205px" role="img" aria-label="Photo of a group of friends on a bench"></div>
    <div class="brand sm" style="right:13px;top:8px"><span class="brand-name">PIXELFORGE</span><span class="brand-tag">TAGLINE HERE</span></div>
    <div class="abs" style="left:192px;top:46px;width:192px;height:121px;background:var(--dark);padding:20px 10px 0 20px;color:#fff">
      <h2 style="font-size:16px;font-weight:600">About Us</h2>
      <div style="width:20px;height:1.5px;background:var(--red);margin:3px 0 8px"></div>
      <p style="font-size:5px;line-height:1.35;color:#ddd">Lorem ipsum dolor sit amet, consectetur adipiscing elit, sed do eiusmod tempor incididunt ut labore et dolore magna aliqua.</p>
      <p style="font-size:5px;line-height:1.35;color:#ddd;margin-top:6px">Ut enimad minim veniam, quis nostrud exercitation ullamco laboris nisi ut aliquip ex ea commodo consequat.</p>
    </div>
    <div class="footer"><span>© 2017 PIXELFORGE All rights reserved</span><span>6</span></div>
  </section>

  <!-- 7 services -->
  <section class="slide">
    <h2 class="slide-title">Our Services</h2>
    <div class="brand sm" style="left:318px;top:9px"><span class="brand-name">PIXELFORGE</span><span class="brand-tag">TAGLINE HERE</span></div>
    <div class="abs" style="left:35px;top:50px;width:149px;height:94px;background:#000"></div>
    <div class="brand on-dark" style="left:35px;top:89px;width:149px"><span class="brand-name" style="font-size:12px">PIXELFORGE</span><span class="brand-tag" style="font-size:5px;margin-top:2px">TAGLINE HERE</span></div>
    <p class="abs" style="left:35px;top:152px;font-size:7.5px;color:#333">Your Title Goes Here</p>
    <p class="lorem abs" style="left:35px;top:161px;width:148px">Lorem ipsum adipiscing elit, sed do eiusmod tempor incididunt ut labore et dolore magna aliqua. Ut enim minim veniam, quis nostrud exercitation ullamco laboris nisi ut aliquip ex ea commodo consequat.</p>
    <div class="service" style="top:50px"><span class="round-icon"><svg width="8" height="8" viewBox="0 0 10 10"><path d="M1 9h8M2 8V6M4 8V4M6 8V5M8 8V2" stroke="#fff"/></svg></span><div><h4>Service Number One</h4><p class="lorem">Lorem ipsum dolor sit amet, consectetur adipiscing elit, sed do eiusmod tempor incididunt ut labore et dolore magna aliqua.</p></div></div>
    <div class="service" style="top:96px"><span class="round-icon"><svg width="8" height="8" viewBox="0 0 10 10"><path d="M2 8l6-6M5 2h3v3" stroke="#fff" fill="none"/></svg></span><div><h4>Service Number Two</h4><p class="lorem">Lorem ipsum dolor sit amet, consectetur adipiscing elit, sed do eiusmod tempor incididunt ut labore et dolore magna aliqua.</p></div></div>
    <div class="service" style="top:142px"><span class="round-icon"><svg width="8" height="8" viewBox="0 0 10 10"><circle cx="4.2" cy="4.2" r="2.6" fill="none" stroke="#fff" stroke-width="1.2"/><path d="M6 6l3 3" stroke="#fff" stroke-width="1.2"/></svg></span><div><h4>Service Number Three</h4><p class="lorem">Lorem ipsum dolor sit amet, consectetur adipiscing elit, sed do eiusmod tempor incididunt ut labore et dolore magna aliqua.</p></div></div>
    <div class="footer"><span>© 2017 PIXELFORGE All rights reserved</span><span>7</span></div>
  </section>

  <!-- 8 quote area -->
  <section class="slide">
    <h2 class="slide-title">Quote Area</h2>
    <div class="brand sm" style="right:13px;top:9px"><span class="brand-name">PIXELFORGE</span><span class="brand-tag">TAGLINE HERE</span></div>
    <div class="photo photo-dark" style="left:0;top:46px;width:192px;height:134px" role="img" aria-label="Darkened photo of friends with a phone"></div>
    <div class="photo photo-green" style="left:192px;top:46px;width:192px;height:134px" role="img" aria-label="Photo of friends laughing outdoors"></div>
    <p class="abs" style="left:23px;top:86px;width:160px;font-size:8.8px;font-weight:300;color:#fff;line-height:1.25">“ Coming together is a beginning.<br>Keeping together is progress.”<br>Working together is success.</p>
    <p class="abs" style="left:32px;top:140px;font-size:6px;color:#ccc">- Walter Grey -</p>
    <div class="footer"><span>© 2017 PIXELFORGE All rights reserved</span><span>8</span></div>
  </section>

  <!-- 9 previous work -->
  <section class="slide">
    <div class="badge" style="left:18px;top:20px;width:50px;height:26px;border-radius:3px"></div>
    <div class="badge" style="left:118px;top:18px;width:52px;height:30px;border-radius:50% / 40%"></div>
    <div class="badge" style="left:216px;top:20px;width:54px;height:26px;background:#333"></div>
    <div class="badge" style="left:308px;top:20px;width:58px;height:22px;border-radius:0 0 12px 12px"></div>
    <div class="badge" style="left:18px;top:86px;width:44px;height:40px;border-radius:50%"></div>
    <div class="badge" style="left:315px;top:92px;width:52px;height:22px;border-radius:11px;border-color:#999"></div>
    <div class="badge" style="left:20px;top:158px;width:40px;height:40px;border-radius:50%"></div>
    <div class="badge" style="left:122px;top:158px;width:42px;height:42px;border-radius:50%"></div>
    <div class="badge" style="left:210px;top:162px;width:70px;height:30px;border-width:0 0 6px;border-color:#333"></div>
    <div class="badge" style="left:312px;top:160px;width:56px;height:34px;border-radius:4px"></div>
    <div class="abs" style="left:97px;top:73px;width:189px;height:69px;background:#000;color:#fff;font-size:17.5px;font-weight:600;display:flex;align-items:center;justify-content:center">Our Previous work</div>
  </section>

  <!-- 10 text area -->
  <section class="slide">
    <h2 class="slide-title">Text Area</h2>
    <div class="brand sm" style="left:318px;top:9px"><span class="brand-name">PIXELFORGE</span><span class="brand-tag">TAGLINE HERE</span></div>
    <div class="abs" style="left:33px;top:68px;width:336px">
      <p class="lead">This is place for your header text. Insert your text here, just replace this text with your own text</p>
      <p class="para" style="margin-top:12px">Lorem ipsum dolor sit amet, consectetur adipiscing elit, sed do eiusmod tempor incididunt ut labore et dolore magna aliqua. Ut enimad minim veniam, quis nostrud exercitation ullamco laboris nisi ut aliquip ex ea commodo consequat.</p>
      <p class="para">Duis aute irure dolor in reprehenderit in voluptate velit esse cillum dolore eu fugiat nulla pariatur. Excepteur sint occaecat cupidatat non proident, sunt inculpa qui officia deserunt mollit anim id est laborum.</p>
      <p class="para">Ut enimad minim veniam, quis nostrud exercitation ullamco laboris nisi ut aliquip ex ea commodo consequat.</p>
    </div>
    <div class="footer"><span>© 2017 PIXELFORGE All rights reserved</span><span>10</span></div>
  </section>

  <!-- 11 vision & mission -->
  <section class="slide">
    <h2 class="slide-title">Our Vision &amp; Mission</h2>
    <div class="brand sm" style="right:13px;top:9px"><span class="brand-name">PIXELFORGE</span><span class="brand-tag">TAGLINE HERE</span></div>
    <div class="photo photo-dark" style="left:0;top:50px;width:384px;height:140px" role="img" aria-label="Darkened photo of a team at work"></div>
    <div class="abs" style="left:20px;top:70px;width:155px;color:#fff">
      <p style="font-size:11px;font-weight:300">• Our Vision:</p>
      <p style="font-size:8.5px;font-weight:700;line-height:1.25;margin-top:2px">Go to the Next Level<br>Without look in the past</p>
      <div style="width:50px;height:1px;background:#fff;margin:7px 0"></div>
      <p style="font-size:4.4px;line-height:1.35;color:#ddd">Lorem ipsum dolor sit amet, consectetur adipiscing elit, sed do eiusmod tempor incididunt ut labore et dolore magna aliqua. Ut enimad minim veniam, quis nostrud exercitation ullamco laboris nisi ut aliquip ex ea commodo consequat.</p>
    </div>
    <div class="abs" style="left:215px;top:70px;width:160px;color:#fff">
      <p style="font-size:11px;font-weight:300">• Our Missions:</p>
      <div style="display:flex;gap:10px;margin-top:5px"><span class="round-icon" style="background:#fff"></span><div><p style="font-size:6px">Your Text Here</p><p style="font-size:4.4px;color:#ddd;line-height:1.3">Lorem ipsum dolor sit amet consectetur adipiscing elit, sed do eiusmod tempo.</p></div></div>
      <div style="display:flex;gap:10px;margin-top:10px"><span class="round-icon" style="background:#fff"></span><div><p style="font-size:6px">Your Text Here</p><p style="font-size:4.4px;color:#ddd;line-height:1.3">Lorem ipsum dolor sit amet consectetur adipiscing elit, sed do eiusmod tempo.</p></div></div>
      <div style="display:flex;gap:10px;margin-top:10px"><span class="round-icon" style="background:#fff"></span><div><p style="font-size:6px">Your Text Here</p><p style="font-size:4.4px;color:#ddd;line-height:1.3">Lorem ipsum dolor sit amet consectetur adipiscing elit, sed do eiusmod tempo.</p></div></div>
    </div>
    <div class="footer"><span>© 2017 PIXELFORGE All rights reserved</span><span>11</span></div>
  </section>

  <!-- 12 text area framed -->
  <section class="slide" style="background:#000">
    <div class="abs" style="left:192px;top:0;width:192px;height:216px;background:var(--red)"></div>
    <div class="abs" style="left:0;top:200px;width:384px;height:16px;background:#000"></div>
    <div class="abs" style="left:13px;top:14px;width:358px;height:190px;background:#fff"></div>
    <h2 class="slide-title" style="left:32px;top:30px">Text Area</h2>
    <p class="abs" style="right:26px;top:42px;font-size:7.5px;font-weight:800;color:var(--ink)">PIXELFORGE</p>
    <div class="abs" style="left:32px;top:80px;width:326px">
      <p class="lead">This is place for your header text. Insert your text here, just replace this text with your own text</p>
      <p class="para" style="font-size:5.3px">Lorem ipsum dolor sit amet, consectetur adipiscing elit, sed do eiusmod tempor incididunt ut labore et dolore magna aliqua. Ut enimad minim veniam, quis nostrud exercitation ullamco laboris nisi ut aliquip ex ea commodo consequat.</p>
      <p class="para" style="font-size:5.3px">Duis aute irure dolor in reprehenderit in voluptate velit esse cillum dolore eu fugiat nulla pariatur. Excepteur sint occaecat cupidatat non proident, sunt inculpa qui officia deserunt mollit anim id est laborum.</p>
      <p class="para" style="font-size:5.3px">Ut enimad minim veniam, quis nostrud exercitation ullamco laboris nisi ut aliquip ex ea commodo consequat. Lorem ipsum dolor sit amet, consectetur adipiscing elit, sed do eiusmod tempor incididunt ut labore et dolore magna aliqua.</p>
    </div>
  </section>

</main>
</body>
</html>
```